Modern Business Card

Modern professional business card with more than just logo and demographic info. Something memorable.

We are a trendy/modern chiropractic group with an emphasis on neurology, hence the minimalist-type brain logo. We want to convey that modern and technical aspect with professionalism and the elite nature of our practice environment.

```html
<!DOCTYPE html>
<html lang="en">
<head>
<meta charset="utf-8">
<title>Orvane Spine – Business Card</title>
<link href="https://fonts.googleapis.com/css2?family=Cinzel:wght@400&family=Lato:wght@400&family=Montserrat:wght@700&display=swap" rel="stylesheet">
<style>
  :root{
    --backdrop:#d2d3ce;
    --card-white:#ffffff;
    --card-black:#181818;
    --brand-blue:#4a80c8;
    --ink:#2b2b2b;
    --ink-soft:#4a4a4a;
    --brand-light:#f2f2f2;
  }
  html,body{margin:0;padding:0;overflow:hidden;}
  body{width:1200px;height:801px;background:var(--backdrop);position:relative;}
  .card{
    position:absolute;top:252px;width:520px;height:297px;box-sizing:border-box;
    border-bottom:4px solid var(--brand-blue);
    box-shadow:0 14px 30px rgba(0,0,0,.25);
  }
  .card--front{left:60px;background:var(--card-white);}
  .card--back{left:620px;background:var(--card-black);}
  .brand{position:absolute;display:flex;align-items:center;gap:10px;}
  .brand__mark{border-radius:50%;background:var(--brand-blue);flex:none;}
  .brand__name{font-family:"Cinzel",serif;font-weight:400;line-height:1;white-space:nowrap;}
  .card--front .brand{left:30px;top:128px;}
  .card--front .brand__mark{width:32px;height:32px;}
  .card--front .brand__name{font-size:22px;color:var(--ink);}
  .card--back .brand{left:0;right:0;top:124px;justify-content:center;}
  .card--back .brand__mark{width:44px;height:44px;}
  .card--back .brand__name{font-size:32px;color:var(--brand-light);}
  .divider{position:absolute;left:250px;top:40px;width:1.5px;height:218px;background:var(--brand-blue);}
  .contact{position:absolute;left:276px;top:52px;font-family:"Lato",sans-serif;color:var(--ink-soft);}
  .contact__name{font-family:"Montserrat",sans-serif;font-weight:700;color:var(--brand-blue);font-size:21px;margin:0;letter-spacing:.3px;}
  .contact__role{font-size:13px;margin:3px 0 14px;}
  .contact__address{font-size:12.5px;line-height:1.45;margin:0 0 14px;}
  .contact__list{list-style:none;margin:0;padding:0;font-size:12.5px;}
  .contact__item{display:flex;align-items:center;gap:9px;margin-bottom:7px;}
  .contact__icon{width:14px;height:14px;flex:none;}
</style>
</head>
<body>
  <section class="card card--front" aria-label="Business card front">
    <div class="brand">
      <span class="brand__mark"></span>
      <span class="brand__name">Orvane Spine</span>
    </div>
    <div class="divider"></div>
    <div class="contact">
      <h1 class="contact__name">JOHN SMITH</h1>
      <p class="contact__role">Founder &amp; CEO</p>
      <p class="contact__address">1234 First Line Address<br>5678 Second Line Address</p>
      <ul class="contact__list">
        <li class="contact__item">
          <svg class="contact__icon" viewBox="0 0 16 16" aria-hidden="true"><path fill="#4a80c8" d="M3.5 1.5l2.3 2.6-1.3 1.6c.9 2 2.2 3.3 4.2 4.2l1.6-1.3 2.6 2.3-1.3 2.3C6.7 13.6 2.4 9.3 1.2 2.8z"/></svg>
          <span>1234567890</span>
        </li>
        <li class="contact__item">
          <svg class="contact__icon" viewBox="0 0 16 16" aria-hidden="true"><rect x="1" y="3" width="14" height="10" fill="#4a80c8"/><path d="M1.5 3.5L8 9l6.5-5.5" fill="none" stroke="#fff" stroke-width="1.2"/></svg>
          <span>info@yourmail.com</span>
        </li>
        <li class="contact__item">
          <svg class="contact__icon" viewBox="0 0 16 16" aria-hidden="true"><circle cx="8" cy="8" r="7" fill="#4a80c8"/><path d="M1 8h14M8 1c-3 3.5-3 10.5 0 14M8 1c3 3.5 3 10.5 0 14" fill="none" stroke="#fff" stroke-width="1"/></svg>
          <span>www.yourwebsite.com</span>
        </li>
      </ul>
    </div>
  </section>

  <section class="card card--back" aria-label="Business card back">
    <div class="brand">
      <span class="brand__mark"></span>
      <span class="brand__name">Orvane Spine</span>
    </div>
  </section>
</body>
</html>
```